Banner 170x60 for Barrel Sauna Rental Banner

Attention, please do every side graphic distance 5cm . It is for attachment.
search for a graphic design in dimension 170x60cm.
we have a barrel sauna rental service and need a banner for the two sides.
please look photos.
big text is: (I CAN RENT ME!!! )in english like: you can rent me
heisse-holzstube.de
015243197720
info@heisse-holzstube.de
we need an eye catcher design!!!!
Design:
maybe wood in at background.
maybe burning fire and sauna style.
Please don't use my barrell sauna pictures. It is only an example for you what we do. The barrel sauna is on build at the moment.

```html
<!DOCTYPE html>
<html lang="en">
<head>
<meta charset="utf-8">
<title>Heisse Holzstube – Rental Banner</title>
<link href="https://fonts.googleapis.com/css2?family=Bebas+Neue&family=Poppins:wght@700&display=swap" rel="stylesheet">
<style>
  :root {
    --stage: #c2c2c2;
    --wood-dark: #4a160c;
    --wood-mid: #7a2a14;
    --flame-red: #d8361a;
    --flame-orange: #f07a1e;
    --flame-yellow: #f6c431;
    --board-light: #f3cfa0;
    --board-mid: #e2a46a;
    --board-edge: #3d1a10;
    --plank-orange: #c9531f;
    --headline: #5a1a0b;
    --ink: #1c0c08;
    --strip: #ffffff;
  }
  * { margin: 0; padding: 0; box-sizing: border-box; }
  html, body { width: 1200px; height: 481px; overflow: hidden; background: var(--stage); }
  .banner {
    position: absolute; left: 108px; top: 67px;
    width: 985px; height: 347px; overflow: hidden;
  }
  .banner__backdrop {
    position: absolute; inset: 0;
    background:
      radial-gradient(ellipse 22% 60% at 92% 45%, var(--flame-orange) 0%, rgba(216,54,26,0.6) 45%, transparent 75%),
      radial-gradient(ellipse 18% 45% at 8% 80%, var(--flame-red) 0%, transparent 70%),
      linear-gradient(to top, var(--flame-yellow) 0%, var(--flame-red) 12%, transparent 30%),
      linear-gradient(to bottom, var(--wood-dark), var(--wood-mid) 60%, var(--wood-dark));
  }
  .brand-plank {
    position: absolute; left: 0; top: 0; width: 190px; height: 134px;
    background: linear-gradient(160deg, var(--plank-orange), #a93c17);
    border-bottom: 10px solid var(--board-edge);
    border-right: 8px solid var(--board-edge);
    display: flex; align-items: center; justify-content: center;
  }
  .brand-plank__name {
    font-family: "Bebas Neue", sans-serif; font-size: 24px;
    color: var(--ink); letter-spacing: 0.5px;
  }
  .sign-board {
    position: absolute; left: 175px; top: 75px; width: 623px; height: 186px;
    border-radius: 8px;
    background: radial-gradient(ellipse 60% 60% at 50% 45%, var(--board-light), var(--board-mid));
    box-shadow: 10px 10px 0 var(--board-edge);
    display: flex; align-items: center; justify-content: center;
    overflow: hidden;
  }
  .sign-board__headline {
    font-family: "Bebas Neue", sans-serif; font-size: 104px; line-height: 1;
    font-weight: 400;
    color: var(--headline); letter-spacing: 1px; white-space: nowrap;
    padding-top: 8px;
  }
  .contact-strip {
    position: absolute; left: 0; top: 285px; width: 985px; height: 41px;
    background: var(--strip);
    display: flex; align-items: center; justify-content: center;
    font-family: "Poppins", sans-serif; font-weight: 700; font-size: 26px;
    color: var(--ink); white-space: nowrap; letter-spacing: -0.3px;
  }
  .contact-strip__sep { margin: 0 7px; font-weight: 400; }
</style>
</head>
<body>
  <section class="banner">
    <div class="banner__backdrop" role="img" aria-label="Dark wooden planks engulfed in orange and yellow flames"></div>
    <div class="brand-plank">
      <span class="brand-plank__name">HEISSE-HOLZSTUBE</span>
    </div>
    <div class="sign-board">
      <h1 class="sign-board__headline">I CAN RENT ME!!!</h1>
    </div>
    <div class="contact-strip">
      <span>heisse-holzstube.de</span><span class="contact-strip__sep">|</span>
      <span>015243197720</span><span class="contact-strip__sep">|</span>
      <span>info@heisse-holzstube.de</span>
    </div>
  </section>
</body>
</html>
```